Design a building access mobile app for Quillo by Tamberlin Entry Systems

Hello, We're looking for an awesome designer to create an app design for our app Quillo, by Tamberlin Entry Systems. the mobile app allows employees open their office doors with their mobile phone. this means they don't have to use those plastic card badges or keys. We like clean modern design, dark and light themes. We don't have a logo yet.
Updates

Reason: Waiting on a couple designers to submit concepts

Target Market(s)

Commercial and employees

Industry/Entity Type

Building

Font styles to use
Sans Serif
Other font styles liked:
• Oswald extra light

Requirements
Must have
• nice clean design

```html
<!DOCTYPE html>
<html lang="en">
<head>
<meta charset="utf-8">
<title>Quillo — Tamberlin Entry Systems</title>
<link rel="stylesheet" href="https://fonts.googleapis.com/css2?family=Oswald:wght@200;300;400&family=Roboto:wght@300;400&display=swap">
<style>
  :root {
    --bg-top: #1f97d3;
    --bg-bottom: #1a7cc4;
    --header-teal: #1fb3c4;
    --header-blue: #1f6fa8;
    --band-blue: #1d6aa3;
    --band-teal: #2a8fae;
    --panel: #ffffff;
    --knob: #4f95dd;
    --ink: #1b2430;
    --ink-soft: #5b6470;
    --rule: #e6eaee;
    --white: #ffffff;
  }
  * { box-sizing: border-box; margin: 0; padding: 0; }
  html, body {
    width: 1200px; height: 864px; overflow: hidden;
  }
  body {
    background: linear-gradient(160deg, var(--bg-top), var(--bg-bottom));
    display: flex; align-items: center; justify-content: center;
    font-family: "Oswald", sans-serif;
  }
  .app-screen {
    width: 420px; height: 746px;
    display: flex; flex-direction: column;
    box-shadow: 0 24px 50px rgba(10, 50, 90, 0.35);
    overflow: hidden;
  }
  .lock-header {
    height: 340px;
    background: linear-gradient(135deg, var(--header-teal) 0%, var(--header-blue) 100%);
    color: var(--white);
    position: relative;
  }
  .status-bar {
    display: flex; justify-content: space-between; align-items: center;
    padding: 6px 10px;
    font-family: "Roboto", sans-serif; font-size: 11px; font-weight: 400;
  }
  .status-bar .signal { display: flex; align-items: center; gap: 4px; }
  .status-bar .battery { display: flex; align-items: center; gap: 4px; }
  .nav-bar {
    display: flex; align-items: center; height: 40px; padding: 0 14px;
    position: relative;
  }
  .nav-title {
    position: absolute; left: 0; right: 0; text-align: center;
    font-weight: 300; font-size: 15px; letter-spacing: 0.5px;
  }
  .lock-status {
    display: flex; flex-direction: column; align-items: center;
    margin-top: 22px;
  }
  .lock-ring {
    width: 122px; height: 122px; border-radius: 50%;
    border: 1.5px solid rgba(255,255,255,0.85);
    display: flex; align-items: center; justify-content: center;
  }
  .lock-label {
    margin-top: 16px; font-weight: 300; font-size: 32px; letter-spacing: 1px;
  }
  .page-dots { display: flex; gap: 10px; margin-top: 18px; align-items: center; }
  .page-dots span { width: 10px; height: 10px; border-radius: 50%; background: rgba(255,255,255,0.55); }
  .page-dots .active { background: transparent; border: 1.5px solid var(--white); width: 12px; height: 12px; }
  .door-control {
    height: 260px; background: var(--panel); position: relative;
    display: flex; align-items: center; justify-content: space-between;
    padding: 0 44px;
  }
  .door-control::before {
    content: ""; position: absolute; left: 0; right: 0; top: 50%;
    border-top: 1px solid var(--rule);
  }
  .door-action {
    position: relative; font-weight: 400; font-size: 19px; letter-spacing: 1px;
  }
  .door-action.open { color: var(--ink); }
  .door-action.close { color: var(--ink-soft); }
  .slider-knob {
    position: absolute; left: 50%; top: 50%; transform: translate(-50%, -50%);
    width: 122px; height: 122px; border-radius: 50%;
    border: 2px solid var(--knob); background: var(--panel);
    display: flex; align-items: center; justify-content: center;
  }
  .slider-knob span {
    width: 98px; height: 98px; border-radius: 50%; background: var(--knob);
  }
  .location-band {
    flex: 1;
    background: linear-gradient(135deg, var(--band-blue) 0%, var(--band-teal) 100%);
    color: var(--white);
    display: flex; align-items: center; justify-content: center;
    font-weight: 300; font-size: 28px; letter-spacing: 1px;
  }
</style>
</head>
<body>
  <main class="app-screen">
    <section class="lock-header">
      <div class="status-bar">
        <div class="signal">
          <svg width="34" height="7" viewBox="0 0 34 7" aria-hidden="true">
            <circle cx="3.5" cy="3.5" r="3" fill="#fff"/>
            <circle cx="10.5" cy="3.5" r="3" fill="#fff"/>
            <circle cx="17.5" cy="3.5" r="3" fill="#fff"/>
            <circle cx="24.5" cy="3.5" r="2.6" fill="none" stroke="#fff" stroke-width="0.8"/>
            <circle cx="31" cy="3.5" r="2.6" fill="none" stroke="#fff" stroke-width="0.8"/>
          </svg>
          <span>Nimbus</span>
          <svg width="12" height="9" viewBox="0 0 12 9" aria-hidden="true">
            <path d="M1 3.5a7 7 0 0 1 10 0M3 5.5a4 4 0 0 1 6 0" fill="none" stroke="#fff" stroke-width="1.2"/>
            <circle cx="6" cy="7.5" r="1" fill="#fff"/>
          </svg>
        </div>
        <span class="clock">1:23 AM</span>
        <div class="battery">
          <span>77%</span>
          <svg width="24" height="11" viewBox="0 0 24 11" aria-hidden="true">
            <rect x="0.5" y="0.5" width="20" height="10" rx="2" fill="none" stroke="#fff"/>
            <rect x="2" y="2" width="13" height="7" rx="1" fill="#fff"/>
            <rect x="21.5" y="3.5" width="2" height="4" rx="1" fill="#fff"/>
          </svg>
        </div>
      </div>
      <nav class="nav-bar">
        <svg width="22" height="16" viewBox="0 0 22 16" aria-label="Menu">
          <path d="M0 2h22M0 8h22M0 14h22" stroke="#fff" stroke-width="1.6"/>
        </svg>
        <h1 class="nav-title">TAMBERLIN ENTRY</h1>
      </nav>
      <div class="lock-status">
        <div class="lock-ring">
          <svg width="56" height="56" viewBox="0 0 56 56" aria-label="Padlock">
            <path d="M16 25v-7a12 12 0 0 1 24 0v7" fill="none" stroke="#fff" stroke-width="6"/>
            <rect x="8" y="24" width="40" height="28" rx="4" fill="#fff"/>
            <circle cx="28" cy="35" r="3.4" fill="#1f8fbb"/>
            <rect x="26.6" y="36" width="2.8" height="7" fill="#1f8fbb"/>
          </svg>
        </div>
        <p class="lock-label">LOCKED</p>
        <div class="page-dots"><span class="active"></span><span></span></div>
      </div>
    </section>
    <section class="door-control">
      <span class="door-action open">OPEN</span>
      <div class="slider-knob"><span></span></div>
      <span class="door-action close">CLOSE</span>
    </section>
    <footer class="location-band">OFFICE LOCATION</footer>
  </main>
</body>
</html>
```